LADIES' HARBOR COLLECTIVE

Design a website for a membership based organization focusing on entrepreneurship, women's issues and global news regarding commerce.
Also, want a news daily tie in to site, and social media outlets.
I want the colors in strong blue, deep or metallic gold and cream/white like logo which will be provided. I want logo altered with globe to replace small sphere in the design.
Also, board members page that should be redesigned. Might need extra coding.
PLEASE SEE http://ladiesharborcollective.example DIDN'T LIKE THIS LAY OUT AT ALL TOO MUCH WHITE AND NOT ENOUGH IMPACT. WANT TO DRAW MEMBERS.

PLEASE SEE http://www.qrtv-sample.example/Index.cfm BUT THIS IS WAY TO BUSY BUT I LIKE THE SLIDING.

SEE OUR TWITTER ACCOUNT FOR INSIGHT. @LADIESHARBCOL

Reason: Happy Holidays. The board approving the design will be out on season time vacation until Jan. 2. Please make any edits requested from designer already submitting layouts. Thank you, Odette

Target Market(s)

GLOBAL BUSINESS WOMEN AND ENTREPRENEURS AGES 20-65

Industry/Entity Type

Media

Number of Pages Required

4 page

Font styles to use
Other font styles liked:
• Baskerville or something similar

Colors
fbed22
3377b5
9bcb3c

Requirements
Must have
• Show diversity of ethnicities if using stock photos. Vibrant and inviting site, MUST JOIN or Be part of this organization. Luxury style
• THIS IS A FOR PROFIT WEBSITE.
• Membership Fees:
• Annual Fee $250
• For an additional fee of $150 you can grow your visibility and voice through our Ladies' Harbor Collective Bulletin and Speaker's Bureau (LHCBSB).
• LHC Speaker's Bureau will support your personal, business and organizations' objectives and to give you greater visibility and voice as an authority world leader or business visionary in your field of service.
• LHCSB realizes that so many worthy leaders' in diverse fields of service are never allowed to be heard. If you feel you are a dynamic speaker, run a worthwhile business or organization and whose wisdom and success can be of service of others sign up today and be part of the LHCSB!
• Student Membership
• Discounted student memberships are also available. Students have access to selected group forums, as well as selected groups of members that provide mentoring. Mentoring helps continue the member's legacy and creates a well spring of future leaders. Student membership fees cost just $75 a year.
• Contact us to help promote you and other women's vision throughout the world.
• Join LHC Now!
• CAN YOU PROVIDE A HEADLINE WITHOUT WOMEN SEE TWITTER ACCOUNT.
Nice to have
• Nice headline and well position tabs.
• Home
• Join LHC Now
• Memberships
• LHC Team Leadership
• About Us
• Contact
• LHC is an Effective Women's Initiative for You!
• New Member - Women's Organization
• 20% Discount- Offer Valid on Your Membership Fee When You Join before 1/30/2105
• Memberships
• LHC Leadership
• At Ladies' Harbor Collective, we offer the opportunity to connect with women throughout the globe. Join these trailblazers to shorten your path to success and camaraderie.
• Who We Are
• Ladies' Harbor Collective is an online women's initiative that promotes your business and visions through social engagement. We are here to help you form strategic partnerships with like-minded women around the world. End your solo journey by becoming a member of LHC.
• LHC also features a forum to promote the services, campaigns, and social activism by our members.
• LHC is about women helping other women. Contact us for more information.
• Learn More about Ladies' Harbor Collective
• Contact us for more information in regards to LHC membership and how to get involved.
• SHARE THIS PAGE:
• twitter, fb, instagram, etc.

```html
<!DOCTYPE html>
<html lang="en">
<head>
<meta charset="utf-8">
<title>Ladies' Harbor Collective</title>
<link href="https://fonts.googleapis.com/css2?family=Open+Sans:wght@400;600;700&family=Libre+Baskerville:wght@400;700&family=Kaushan+Script&display=swap" rel="stylesheet">
<style>
:root{
  --gold:#f2c318;
  --gold-dark:#d9a70c;
  --blue:#0a6fc2;
  --blue-dark:#0d4f8c;
  --sky:#3fa7f1;
  --cream:#efece6;
  --ink:#333;
  --muted:#666;
  --white:#fff;
}
*{box-sizing:border-box;margin:0;padding:0}
html,body{width:881px;height:1200px;overflow:hidden;background:var(--white)}
body{font-family:'Open Sans',sans-serif;color:var(--ink);position:relative}
.topline{height:3px;background:var(--gold)}
.header{height:91px;position:relative}
.brand{position:absolute;left:72px;top:62px;display:flex;align-items:center;gap:5px}
.brand-dot{width:11px;height:11px;border-radius:50%;background:var(--gold)}
.brand-name{font-size:11px;font-weight:600;color:#222;letter-spacing:-.2px}
.brand-tag{position:absolute;left:72px;top:77px;font-size:4px;font-weight:700;color:#222;letter-spacing:.1px}
.btn-top{position:absolute;top:13px;height:29px;font-size:8.5px;font-weight:600;color:var(--white);display:flex;align-items:center;justify-content:center;border-bottom:2px solid rgba(0,0,0,.15)}
.btn-register{left:612px;width:68px;background:var(--blue)}
.btn-member{left:689px;width:119px;background:var(--gold)}
.nav{position:absolute;top:67px;left:350px;font-size:9px;color:#666}
.nav a{position:absolute;white-space:nowrap;text-decoration:none;color:inherit}
.nav a.active{color:var(--blue)}
.hero{position:absolute;top:94px;left:0;width:881px;height:366px;background:radial-gradient(ellipse at 75% 30%,#a9d4f3 0%,#5aa6e4 35%,#1f7ed0 70%,#1169bd 100%)}
.hero-photo{position:absolute;left:410px;top:20px;width:471px;height:346px;background:linear-gradient(90deg,rgba(40,40,50,0) 0%,rgba(40,40,50,.55) 30%,rgba(35,35,45,.6) 100%)}
.hero-title{position:absolute;left:95px;top:84px;font-family:'Libre Baskerville',serif;font-weight:400;font-size:27px;line-height:38px;color:var(--white)}
.hero-title .acr{color:var(--gold);font-weight:700;font-size:34px}
.hero-script{position:absolute;left:93px;top:160px;font-family:'Kaushan Script',cursive;font-size:34px;color:var(--gold)}
.hero-btn{position:absolute;left:95px;top:221px;width:140px;height:40px;background:var(--gold);color:var(--white);font-family:'Libre Baskerville',serif;font-size:13px;display:flex;align-items:center;justify-content:center;border-bottom:2px solid var(--gold-dark)}
.arrow{position:absolute;top:173px;width:19px;height:19px;border-radius:50%;background:var(--white)}
.arrow svg{display:block}
.intro{position:absolute;top:460px;left:0;width:881px;height:132px;background:var(--cream);border-bottom:1px solid #ddd}
.intro-head{position:absolute;left:72px;top:24px;font-size:21px;line-height:28px;font-weight:600;color:#333}
.col{position:absolute;top:26px;width:200px}
.col h3{font-size:19px;font-weight:400;color:var(--blue-dark);margin-bottom:12px}
.col p{font-size:8.5px;line-height:16px;color:#666}
.who{position:absolute;top:593px;left:0;width:881px;height:290px;background:var(--cream)}
.who h2{position:absolute;left:72px;top:25px;font-size:21px;font-weight:600;color:#333}
.who-text{position:absolute;left:72px;top:73px;width:320px;font-size:8.8px;line-height:16px;color:#555}
.who-text p{margin-bottom:9px}
.who-btn{position:absolute;left:72px;top:209px;width:278px;height:35px;background:var(--gold);color:var(--white);font-size:10px;font-weight:600;display:flex;align-items:center;justify-content:center;border-bottom:2px solid var(--gold-dark)}
.who-frame{position:absolute;left:438px;top:33px;width:371px;height:216px;background:var(--white);padding:6px}
.who-photo{width:100%;height:100%;background:linear-gradient(90deg,#9db3cf 0%,#dfe4ea 45%,#ece6de 70%,#b9c5d4 100%)}
.tweets{position:absolute;top:883px;left:0;width:881px;height:149px;background:var(--sky);color:var(--white)}
.tweets h2{text-align:center;font-size:21px;font-weight:600;padding-top:21px}
.tweet{position:absolute;top:75px;display:flex;gap:10px;width:330px}
.tweet-icon{flex:none;width:40px;height:40px;border-radius:50%;background:var(--blue);display:flex;align-items:center;justify-content:center}
.tweet p{font-size:9px;line-height:14.5px;padding-top:2px}
.contact{position:absolute;top:1032px;left:0;width:881px;height:98px;text-align:center;padding-top:27px;font-size:18.5px;line-height:22px;font-weight:700;color:#333}
.contact u{text-underline-offset:3px}
.footer{position:absolute;top:1130px;left:0;width:881px;height:70px;background:var(--gold);border-top:2px solid #f5d35a}
.footer-text{position:absolute;left:72px;top:32px;font-size:7px;color:var(--white)}
.social{position:absolute;top:24px;display:flex;gap:5px;left:711px}
.social span{width:20px;height:20px;background:#a08a4f;border-radius:2px}
</style>
</head>
<body>
<div class="topline"></div>
<header class="header">
  <div class="brand"><span class="brand-dot"></span><span class="brand-name">Ladies' Harbor Collective</span></div>
  <div class="brand-tag">PROFITABLE AND PURPOSEFUL SOCIAL ENGAGEMENT</div>
  <a class="btn-top btn-register">REGISTER</a>
  <a class="btn-top btn-member">BECOME A MEMBERSHIP</a>
  <nav class="nav">
    <a class="active" style="left:0">HOME</a>
    <a style="left:47px">ABOUT US</a>
    <a style="left:111px">PARTNERS</a>
    <a style="left:176px">CAREER</a>
    <a style="left:229px">MEMBERSHIPS</a>
    <a style="left:310px">NEWS</a>
    <a style="left:355px">GALLERY</a>
    <a style="left:412px">CONTACTS</a>
  </nav>
</header>

<section class="hero">
  <div class="hero-photo" role="img" aria-label="Group of four smiling businesswomen in suits, arms crossed"></div>
  <h1 class="hero-title"><span class="acr">LHC</span> is an Effective<br>Women's Initiative</h1>
  <div class="hero-script">for You!</div>
  <a class="hero-btn">LEARN MORE</a>
  <span class="arrow" style="left:16px"><svg width="19" height="19"><path d="M11 6 L7.5 9.5 L11 13" stroke="#333" stroke-width="2" fill="none"/></svg></span>
  <span class="arrow" style="left:850px"><svg width="19" height="19"><path d="M8 6 L11.5 9.5 L8 13" stroke="#333" stroke-width="2" fill="none"/></svg></span>
</section>

<section class="intro">
  <h2 class="intro-head">LHC IS AN EFFECTIVE<br>WOMEN'S INITIATIVE<br>FOR YOU!</h2>
  <div class="col" style="left:373px"><h3>Memberships</h3><p>At Ladies' Harbor Collective, we offer the opportunity to connect with women through out the globe.</p></div>
  <div class="col" style="left:622px"><h3>LHC Leadership</h3><p><span style="color:#111">Join</span> these trailblazers to shorten your path to success and camaraderie</p></div>
</section>

<section class="who">
  <h2>WHO WE ARE</h2>
  <div class="who-text">
    <p>Ladies' Harbor Collective is an online women's initiative that promotes your business and visions through social engagement. We are here to help you form strategic partnerships with like-minded women around the world. End your solo journey by becoming a member of LHC.</p>
    <p>LHC also features a forum to promote the services, campaigns, and social activism by our members. LHC is about women helping other women. Contact us for more information.</p>
  </div>
  <a class="who-btn">LEARN MORE ABOUT LADIES' HARBOR COLLECTIVE</a>
  <div class="who-frame"><div class="who-photo" role="img" aria-label="Smiling businesswoman in front of blurred colleagues in an office"></div></div>
</section>

<section class="tweets">
  <h2>LATEST TWEET NEWS</h2>
  <div class="tweet" style="left:72px">
    <span class="tweet-icon"><svg width="16" height="14" viewBox="0 0 16 14"><path d="M2 1 H14 Q15 1 15 2 V9 Q15 10 14 10 H7 L3 13 V10 H2 Q1 10 1 9 V2 Q1 1 2 1Z" fill="#fff"/></svg></span>
    <p>The online crowd seems to have #Varnholt mass kidnapping fatigue. About 200 men, women &amp; children have been snatched from Kestrelby.</p>
  </div>
  <div class="tweet" style="left:475px">
    <span class="tweet-icon"><svg width="16" height="14" viewBox="0 0 16 14"><path d="M2 1 H14 Q15 1 15 2 V9 Q15 10 14 10 H7 L3 13 V10 H2 Q1 10 1 9 V2 Q1 1 2 1Z" fill="#fff"/></svg></span>
    <p>We should just stop using the word #innovation &amp; related cliches until we have equality for women in the #tech &amp; #VC workplace. Seriously.</p>
  </div>
</section>

<section class="contact"><u>CONTACT US</u> FOR MORE INFORMATION IN REGARDS TO<br>LHC MEMBERSHIP AND HOW TO GET INVOLVED.</section>

<footer class="footer">
  <div class="footer-text">©2014 all copyrights are reserved &nbsp;Ladies' Harbor Collective Terms of Service - Privacy Policy</div>
  <div class="social"><span></span><span></span><span></span><span></span></div>
</footer>
</body>
</html>
```